Business Card Design Project : Ridgeline Press

In preparation for market launch, Tamarind's Ridgeline Press require the development of a business card. Ridgeline Press is a Community online publishing web portal. We provide the the city of Whistler located in B.C. (Canada) business directories, News, Classified ads, News, Events and blogs etc.

The main focus of the brand is to help local businesses to corporate with their online advertisement and marketing. Meeting our clients face to face is a must (B2B).

Target Market(s)

The target market is B2B customers. Business Owners to Marketing, advertising Managers

Industry/Entity Type

Business

Requirements
Must have
• - The business card will be two sided.
the BACK side will have our logo which consist of (icon, url,slogan) submited. The logo will be middle and centred.

The FRONT side should have company details:

Company Legal Name: TAMARIND RIDGELINE MEDIA

Owen Farsk
Director of Sales & Marketing

www.tamarindridgeline.biz
owen@tamarindridgeline.biz

Phone: 604 317 8842
#2714 - 582 E. Halvern St.
Vancouver, B.C. V7K2R4 Canada
Nice to have
• - For the "FRONT" side of our business card. You can separate or re-arrange with our logo components (icon, logo,slogan). It does not have to be together.

Also our company legal name is rather long so arrange or organize the name in a way to make it shorter. Your experience and creativity will have to come in play.
Should not have
• should not have other colors beside logo color and black text (2 colors). Also nothing Three dimensional

```html
<!DOCTYPE html>
<html lang="en">
<head>
<meta charset="utf-8">
<title>Ridgeline Press – Business Card</title>
<link rel="stylesheet" href="https://fonts.googleapis.com/css2?family=Source+Sans+3:wght@400;600;700&display=swap">
<style>
  :root {
    --brand-blue: #2a7cc7;
    --ink: #111111;
    --paper: #ffffff;
    --stage: #e9ecef;
  }
  * { margin: 0; padding: 0; box-sizing: border-box; }
  html, body { width: 1200px; height: 900px; overflow: hidden; }
  body {
    background: var(--stage);
    font-family: "Source Sans 3", "Helvetica Neue", Arial, sans-serif;
    position: relative;
  }
  .card {
    position: absolute;
    left: 280px;
    width: 640px;
    height: 366px;
    overflow: hidden;
  }
  .card--back { top: 70px; background: var(--brand-blue); }
  .card--front { top: 470px; background: var(--paper); }

  /* Back side */
  .back-lockup {
    position: absolute;
    inset: 0;
    display: flex;
    flex-direction: column;
    align-items: center;
    justify-content: center;
    gap: 6px;
  }
  .back-lockup .brand-row { display: flex; align-items: center; gap: 14px; }
  .brand-dot { width: 26px; height: 26px; border-radius: 50%; background: var(--paper); flex: none; }
  .brand-url { font-weight: 700; font-size: 34px; color: var(--ink); letter-spacing: -0.3px; white-space: nowrap; }
  .back-lockup .slogan { font-size: 24px; color: var(--paper); }

  /* Front side */
  .front-band { position: absolute; inset: 0; z-index: 0; }
  .company-name {
    position: absolute;
    left: 28px; top: 20px;
    font-weight: 700; font-size: 28px;
    color: var(--brand-blue);
    z-index: 1;
  }
  .contact {
    position: absolute;
    left: 28px; top: 100px;
    color: var(--paper);
    font-size: 14px;
    line-height: 1.45;
    z-index: 1;
  }
  .contact .person { font-weight: 700; font-size: 22px; line-height: 1.1; }
  .contact .role { margin-bottom: 10px; }
  .contact .label { font-weight: 700; }
  .contact .address { margin-top: 8px; }

  .front-lockup {
    position: absolute;
    right: 28px; top: 220px;
    text-align: left;
    z-index: 1;
  }
  .front-lockup .brand-row { display: flex; align-items: center; gap: 10px; }
  .front-lockup .brand-dot { width: 20px; height: 20px; background: var(--brand-blue); }
  .front-lockup .brand-url { font-size: 26px; }
  .front-lockup .slogan { font-size: 19px; color: var(--brand-blue); padding-left: 30px; }
</style>
</head>
<body>

  <section class="card card--back" aria-label="Card back">
    <div class="back-lockup">
      <div class="brand-row">
        <span class="brand-dot"></span>
        <span class="brand-url">www.tamarindridgeline.biz</span>
      </div>
      <div class="slogan">Your information gateway</div>
    </div>
  </section>

  <section class="card card--front" aria-label="Card front">
    <svg class="front-band" width="640" height="366" viewBox="0 0 640 366" aria-hidden="true">
      <polygon points="0,70 300,70 220,340 0,340" fill="var(--brand-blue)"/>
    </svg>
    <h1 class="company-name">Ridgeline Press</h1>
    <div class="contact">
      <div class="person">Owen Farsk</div>
      <div class="role">Director of Sales &amp; Marketing</div>
      <div><span class="label">p:</span> 604 317 8842</div>
      <div><span class="label">e:</span> owen@tamarindridgeline.biz</div>
      <div><span class="label">w:</span> www.tamarindridgeline.biz</div>
      <div class="address">#2714 - 582 E. Halvern St.<br>Vancouver, B.C. V7K2R4 Canada</div>
    </div>
    <div class="front-lockup">
      <div class="brand-row">
        <span class="brand-dot"></span>
        <span class="brand-url">www.tamarindridgeline.biz</span>
      </div>
      <div class="slogan">Your information gateway</div>
    </div>
  </section>

</body>
</html>
```